Bluefern Business Services needs a new interactive and interesting website

We need an interesting, professional, modern and functional company website for Bluefern Business Services - a young IT Services company based out of Chennai, India.

Bluefern Business Services is a fully owned subsidiary of Marlow Goods, one of the world's leading direct to consumer wine merchant.

We already have a registered company logo which must feature in the website.

We conceive, design, develop, test, implement and support IT solutions across the entire Marlow Goods IT landscape. For ex : We currently run about 25 e-commerce websites for Marlow Goods on ATG and Dot Net.

We would like to see our corporate colors used in the website. (Burgundy wine and wine green - source: www.bluefernbs-site.com)

We are looking at this website to communicate a fun, friendly and professionally managed company - reaching out to career seekers, prospective customers and general public.

For reference - The company name 'Bluefern' is an inspiration from the Marlow Goods lineage.

The second image with the world map is stickered on our main entrance to the office, I am not sure where this can be used -just putting it out there..

Please note that there are only a few more days to submit designs for this contest  !

I would appreciate if you can help posting your designs in time for our review and consideration.

Thanks.

Reason: Thanks for your inputs. We have a number of designers and a lot to digest and work with in the past few days. There has been a rush of new designs in the last few days Hence we will require more time to process these and make our decision. Hence i am requesting the contest to be open for more days. Regards, Tarun

Target Market(s)

Prospective job seekers who want to know more about the company and also wish to apply for a job vacancy
People wanting to know more about the company in general and our progress
People who want to see what we offer and how we can help them too - prospective customers
Companies that are interested in our IT Captive journey and are looking for a business opportunity

Industry/Entity Type

E-Commerce

Requirements
Must have
• Log In/ Register facility acting as a Single Sign on for Intranet (Employees)

Facility to post job vacancies (with an expiry date) and enable people to apply for a role and upload their CV/Resume.

Facility to Review Job applications

Facility for website visitors to contact Bluefern business Services via an online 'Contact Us' form with a split of job seekers and business opportunities

Gallery facility to upload pictures regarding company events
Nice to have
• Less Cluttered and contemporary design
Some Wine/Vineyard inspirations will be good but not too much, the company is an IT services company

```html
<!DOCTYPE html>
<html lang="en">
<head>
<meta charset="utf-8">
<title>Bluefern Business Services</title>
<link rel="stylesheet" href="https://fonts.googleapis.com/css2?family=Open+Sans:wdth,wght@75..100,400..700&family=Arimo:wght@400;700&display=swap">
<style>
:root{
  --burgundy:#7b0f3b;
  --burgundy-dark:#650a30;
  --green:#86b034;
  --green-dark:#5f8c1d;
  --green-text:#8aa82a;
  --ink:#333;
  --grey:#555;
  --rule:#dcdcdc;
  --band:#e5e5e5;
  --footer:#222;
}
*{box-sizing:border-box;margin:0;padding:0}
html,body{width:1010px;height:1200px;overflow:hidden;background:#fff}
body{position:relative;font-family:"Arimo",Arial,sans-serif;color:var(--ink)}
.abs{position:absolute}
h2{font-family:"Open Sans",sans-serif;font-weight:600;font-size:19px;font-stretch:82%;color:#4a4a4a;letter-spacing:0;white-space:nowrap}

.logo{left:121px;top:19px;width:138px;height:69px;background:var(--burgundy);color:#fff;display:flex;flex-direction:column;justify-content:center;padding-left:18px}
.logo b{font-family:"Open Sans",sans-serif;font-size:19px;font-weight:700;line-height:1}
.logo span{font-family:"Open Sans",sans-serif;font-size:10.5px;margin-top:2px}

.notice{left:504px;top:30px;width:387px;height:48px;background:var(--burgundy);border-radius:4px;color:#fff;font-family:"Open Sans",sans-serif;font-size:9.3px;font-stretch:88%;line-height:19px;padding:5px 9px;white-space:nowrap}
.notice:after{content:"";position:absolute;left:25px;bottom:-9px;border:9px solid transparent;border-bottom:0;border-top-color:var(--burgundy)}

.nav{left:0;top:107px;width:1010px;height:36px;background:linear-gradient(#96bf44,#6e9b25);border-top:1px solid #c3d98d;border-bottom:1px solid #557c18}
.nav a{position:absolute;top:0;height:35px;line-height:35px;text-align:center;color:#fff;font-family:"Open Sans",sans-serif;font-weight:600;font-size:10.5px;text-decoration:none;border-right:1px solid #7da433}
.nav a.active{background:#6b7a2a}
.search{left:668px;top:6px;width:218px;height:25px;background:linear-gradient(#f3f6ea,#fff);border:1px solid #a7c26a}
.search-btn{right:0;top:0;width:28px;height:23px;background:var(--green-dark)}

.hero{left:0;top:143px;width:1010px;height:297px;background:linear-gradient(180deg,#8c9a4a 0%,#c6b95a 30%,#b8a43a 55%,#7c8a32 80%,#5b6e2a 100%)}
.hero-title{left:121px;top:75px;font-family:"Open Sans",sans-serif;font-size:24px;font-stretch:92%;color:var(--burgundy);letter-spacing:-.3px;white-space:nowrap}
.hero-sub{left:121px;top:110px;font-family:"Open Sans",sans-serif;font-size:19px;font-stretch:92%;color:var(--burgundy);white-space:nowrap}
.hero-text{left:121px;top:143px;width:340px;font-family:"Open Sans",sans-serif;font-size:11.5px;font-stretch:88%;line-height:19px;color:#4a4520}
.dots{left:121px;top:215px;display:flex;gap:5px}
.dots i{width:11px;height:11px;border-radius:50%;background:#9b9b8a;display:block}
.dots i:first-child{background:var(--burgundy)}
.devices{left:596px;top:168px;width:245px;height:234px;background:linear-gradient(135deg,#2a2a2a,#444);border-radius:8px}

.welcome h2{left:121px;top:459px}
.rule{height:1px;background:var(--rule)}
.photo-team{left:121px;top:515px;width:204px;height:175px;background:linear-gradient(135deg,#d8dcd6,#8d8f8a 60%,#3c3c3c)}
.welcome-text{left:332px;top:512px;width:285px;font-size:10px;line-height:13px;color:var(--grey);text-align:justify}
.welcome-text h3{font-weight:400;font-size:10.5px;color:var(--burgundy);margin-bottom:12px}
.welcome-text p{margin-bottom:12px}

.arrows{display:flex;gap:1px}
.arrows i{width:18px;height:18px;background:#2a2a2a;color:#e27a1a;font-style:normal;font-size:9px;line-height:18px;text-align:center}

.testi-photo{left:657px;top:518px;width:78px;height:68px;background:linear-gradient(135deg,#c9b6a4,#9e8673)}
.testi-short{left:742px;top:518px;width:148px;font-size:9.8px;line-height:13.5px;color:var(--grey);text-align:justify}
.testi-long{left:655px;top:599px;width:236px;font-size:10px;line-height:13.5px;color:var(--grey);text-align:justify}
.testi-sign{left:655px;top:665px;font-size:10px;line-height:13.5px;color:var(--grey)}
.testi-sign span{color:var(--green-text)}

.divider{left:121px;top:717px;width:770px;height:3px;background:#d8d8d2;border-radius:2px}
.col-sep{top:741px;width:4px;height:269px;background:#dcdcd4}

.services-intro{left:120px;top:796px;width:238px;font-size:10px;line-height:14px;color:var(--ink);text-align:justify}
.svc-list{left:122px;top:850px;list-style:none;font-size:9.8px;color:var(--ink)}
.svc-list li{height:29.2px;display:flex;align-items:flex-start}
.svc-list li:before{content:"›";width:8px;height:8px;border-radius:50%;background:#222;color:#fff;font-size:8px;line-height:7px;text-align:center;margin:2px 9px 0 0;flex:none}

.opp{left:380px;width:245px;height:60px}
.opp-date{left:0;top:0;width:56px;height:56px;border-radius:50%;background:#555;color:#fff;font-family:"Open Sans",sans-serif;font-size:15px;line-height:19px;text-align:center;padding-top:9px}
.opp-body{left:64px;top:0;width:190px}
.opp-body h4{font-weight:400;font-size:9.8px;color:var(--ink);white-space:nowrap}
.opp-body p{font-size:7.6px;color:#666;margin-top:9px;white-space:nowrap}
.opp-body a{display:block;font-size:8px;font-weight:700;color:var(--burgundy);margin-top:6px;text-decoration:none}
.pager{left:442px;top:996px;display:flex;gap:4px}
.pager i{width:13px;height:13px;border-radius:50%;background:#cfcfcf;display:block}

.video{left:656px;top:801px;width:236px;height:190px;background:linear-gradient(135deg,#eef0ee,#b8bcc0 50%,#5a5f66)}
.video-bar{left:656px;top:991px;width:236px;height:13px;background:linear-gradient(#fafafa,#d6d6d6);border:1px solid #999}

.clients{left:0;top:1034px;width:1010px;height:92px;background:var(--band);border-bottom:2px solid #cfcfcf}
.clients-label{left:165px;top:38px;font-family:"Open Sans",sans-serif;font-size:11px;font-weight:600;color:#333}
.client{top:28px;height:36px;display:flex;align-items:center;font-family:"Open Sans",sans-serif;font-weight:600;color:var(--burgundy);white-space:nowrap}

.footer{left:0;top:1150px;width:1010px;height:50px;background:var(--footer)}
.copy{left:122px;top:19px;font-size:9.5px;color:var(--green-text)}
.social{top:13px;width:24px;height:24px;border-radius:50%;background:#3a3a3a}
</style>
</head>
<body>

<header>
  <div class="abs logo"><b>bluefern</b><span>Business Services</span></div>
  <div class="abs notice">Current Opportunities : There are often a number of opportunties available at Bluefern.<br>Here are the latest ones. Be sure to get your application form in before the closing date!</div>
</header>

<nav class="abs nav">
  <a class="active" style="left:121px;width:97px">HOME</a>
  <a style="left:218px;width:143px">ABOUT BLUEFERN</a>
  <a style="left:361px;width:104px">SERVICES</a>
  <a style="left:465px;width:101px">CAREERS</a>
  <a style="left:566px;width:98px;border-right:0">CONTACT</a>
  <div class="abs search">
    <div class="abs search-btn">
      <svg width="28" height="23" viewBox="0 0 28 23"><circle cx="12" cy="10" r="4" fill="none" stroke="#fff" stroke-width="2"/><line x1="15" y1="13" x2="19" y2="17" stroke="#fff" stroke-width="2.5"/></svg>
    </div>
  </div>
</nav>

<section class="abs hero">
  <div class="abs hero-title">Typinon habent claritatem</div>
  <div class="abs hero-sub">Duis autem vel eum iriure dolor</div>
  <p class="abs hero-text">Ut wisi enim ad minim veniam, quis nostrud exerci tation ullamcor per suscipit lobortis nisl ut aliquip ex ea commodo consequat. Dus autem vel eum iriure dolor.</p>
  <div class="abs dots"><i></i><i></i><i></i><i></i></div>
</section>
<div class="abs devices" role="img" aria-label="Two tablets showing the Bluefern website"></div>

<section class="welcome">
  <h2 class="abs">WELCOME!</h2>
  <div class="abs rule" style="left:121px;top:496px;width:496px"></div>
  <div class="abs photo-team" role="img" aria-label="Two colleagues working at a laptop"></div>
  <div class="abs welcome-text">
    <h3>Delivering IT Excellence</h3>
    <p>Welcome to Bluefern Business Services, an emerging provider of global IT consulting and software services. We are part of the Marlow Goods group, a family run business and the world's largest multi-channel home delivery wine merchant...</p>
    <p>Nemo enim ipsam voluptatem quia voluptas sit aspernatur aut odit aut fugit,</p>
    <p style="margin-top:22px">Services, an emerging provider of global IT consulting and software services. We are part of the Marlow Goods group, a family run business and the world's largest multi-channel home deliv-</p>
  </div>
</section>

<section class="testimonials">
  <h2 class="abs" style="left:657px;top:460px">TESTIMONIALS</h2>
  <div class="abs arrows" style="left:854px;top:463px"><i>&lt;</i><i>&gt;</i></div>
  <div class="abs rule" style="left:657px;top:497px;width:233px"></div>
  <div class="abs testi-photo" role="img" aria-label="Portrait of the client quoted"></div>
  <p class="abs testi-short">Marlow Goods IT landscape. Current plans to strategically transform this landscape to a single set of global systems are underway, across all locations</p>
  <p class="abs testi-long">Marlow Goods IT landscape. Current plans to strategically transform this landscape to a single set of global systems are underway, across all locations and all four continents.</p>
  <p class="abs testi-sign">Thanks<br><span>Daniel</span></p>
</section>

<div class="abs divider"></div>

<section class="services">
  <h2 class="abs" style="left:120px;top:743px">SERVICES</h2>
  <div class="abs arrows" style="left:319px;top:747px"><i>&lt;</i><i>&gt;</i></div>
  <div class="abs rule" style="left:120px;top:780px;width:236px"></div>
  <p class="abs services-intro">The services we provide enable the businesses we support to efficiently manage key functions, including order management.</p>
  <ul class="abs svc-list">
    <li>Packaged Applications</li>
    <li>Enterprise Application Integration</li>
    <li>Digital Commerce</li>
    <li>Application Development &amp; Maintenance</li>
    <li>Multiple versions of Corvane Commerce</li>
    <li>Ledgerline Suite 2009</li>
  </ul>
</section>
<div class="abs col-sep" style="left:370px"></div>

<section class="opportunities">
  <h2 class="abs" style="left:385px;top:743px">LATEST OPPORTUNITIES</h2>
  <div class="abs arrows" style="left:587px;top:747px"><i>&lt;</i><i>&gt;</i></div>
  <div class="abs rule" style="left:385px;top:780px;width:238px"></div>
  <div class="abs opp" style="top:791px"><div class="abs opp-date">Jan<br>07</div><div class="abs opp-body"><h4>Software Developers/Programmer Analysts</h4><p>LX We are looking for a LX Software Developer join...</p><a>read more &gt;&gt;</a></div></div>
  <div class="abs opp" style="top:861px"><div class="abs opp-date">Jan<br>07</div><div class="abs opp-body"><h4>Software Developers/Programmer Analysts</h4><p>LX We are looking for a LX Software Developer join...</p><a>read more &gt;&gt;</a></div></div>
  <div class="abs opp" style="top:931px"><div class="abs opp-date">Jan<br>07</div><div class="abs opp-body"><h4>Software Developers/Programmer Analysts</h4><p>LX We are looking for a LX Software Developer join...</p><a>read more &gt;&gt;</a></div></div>
  <div class="abs pager"><i></i><i></i></div>
</section>
<div class="abs col-sep" style="left:636px"></div>

<section class="events">
  <h2 class="abs" style="left:656px;top:743px">RECENT EVENTS</h2>
  <div class="abs arrows" style="left:854px;top:747px"><i>&lt;</i><i>&gt;</i></div>
  <div class="abs rule" style="left:656px;top:780px;width:234px"></div>
  <div class="abs video" role="img" aria-label="Video still of a team meeting with a presenter">
    <svg class="abs" style="left:102px;top:80px" width="40" height="40" viewBox="0 0 40 40"><circle cx="20" cy="20" r="20" fill="#333" fill-opacity=".75"/><path d="M15 11 L30 20 L15 29Z" fill="#fff"/></svg>
  </div>
  <div class="abs video-bar">
    <svg width="234" height="11" viewBox="0 0 234 11"><path d="M5 3 L9 5.5 L5 8Z" fill="#000"/><text x="17" y="8.5" font-size="7" font-family="Arial" font-weight="700">00:01</text><rect x="48" y="4" width="110" height="3" fill="#888"/><text x="163" y="8.5" font-size="7" font-family="Arial" font-weight="700">100 %</text><rect x="196" y="2" width="7" height="7" fill="none" stroke="#000"/><rect x="212" y="3" width="16" height="5" fill="#555"/></svg>
  </div>
</section>

<section class="abs clients">
  <svg class="abs" style="left:121px;top:27px" width="24" height="26" viewBox="0 0 24 26"><rect x="0" y="0" width="7" height="26" fill="#8cc63e"/><rect x="8" y="8" width="7" height="18" fill="#2e9ad6"/><rect x="16" y="13" width="7" height="13" fill="#f29a1d"/></svg>
  <div class="abs clients-label">OUR CLIENTS</div>
  <div class="abs" style="left:252px;top:26px;width:1px;height:40px;background:#ccc"></div>
  <div class="abs client" style="left:288px;font-size:11px">Southland Cellars</div>
  <div class="abs client" style="left:422px;font-size:11px">Vinotela Casa</div>
  <div class="abs client" style="left:553px;font-size:12px">Harbour Vine Folk</div>
  <div class="abs client" style="left:696px;font-size:14px">Marlow Goods</div>
  <div class="abs client" style="left:811px;font-size:12px">Crimson Wines</div>
</section>

<footer class="abs footer">
  <div class="abs copy">© 2014 bluefernbs.. All Rights Reserved.</div>
  <div class="abs social" style="left:778px"></div>
  <div class="abs social" style="left:806px"></div>
  <div class="abs social" style="left:838px"></div>
  <div class="abs social" style="left:866px"></div>
</footer>

</body>
</html>
```